Kelo Wave Mint Business cards

Logo, tag line and photo on card
Agent Name
Title
Address
Phone number
Email
Website
Make logo on one side large by rotating  to portrait format.  Keep the background of the logo white.

Contact Information for Business Card
Slogan; Making Every Wave Count

```html
<!DOCTYPE html>
<html lang="en">
<head>
<meta charset="utf-8">
<title>Kelo Wave Mint Business Cards</title>
<link href="https://fonts.googleapis.com/css2?family=Montserrat:wght@700;800&family=Open+Sans:wght@400;600;700&display=swap" rel="stylesheet">
<style>
  :root {
    --stage: #222222;
    --red: #c1232a;
    --navy: #24346a;
    --white: #ffffff;
    --ink: #111111;
  }
  * { box-sizing: border-box; margin: 0; padding: 0; }
  html, body { width: 1200px; height: 780px; overflow: hidden; }
  body {
    background: var(--stage);
    position: relative;
    font-family: "Open Sans", sans-serif;
  }
  .card {
    position: absolute;
    top: 232px;
    width: 540px;
    height: 315px;
    border-radius: 20px;
    overflow: hidden;
  }
  .card--back { left: 40px; background: var(--red); }
  .card--front { left: 620px; background: var(--white); }

  .brand-stack {
    position: absolute;
    font-family: "Open Sans", sans-serif;
    font-weight: 700;
    color: var(--navy);
    line-height: 0.95;
  }
  .card--back .brand-stack {
    left: 0; right: 0; top: 78px;
    text-align: center;
    font-size: 54px;
    color: var(--white);
  }
  .card--front .brand-stack {
    left: 28px; top: 26px;
    font-size: 30px;
  }

  .card-art { position: absolute; inset: 0; width: 100%; height: 100%; }

  .corner-tab {
    position: absolute; right: 0; top: 0;
    width: 26px; height: 58px;
    background: var(--navy);
  }
  .person {
    position: absolute; right: 36px; top: 20px;
    text-align: right;
  }
  .person-name {
    font-family: "Montserrat", sans-serif;
    font-weight: 800;
    font-size: 27px;
    line-height: 1;
  }
  .person-name .first { color: var(--red); }
  .person-name .last { color: var(--navy); }
  .person-title {
    font-family: "Montserrat", sans-serif;
    font-weight: 700;
    font-size: 14px;
    color: var(--ink);
    margin-top: 2px;
  }
  .portrait {
    position: absolute;
    left: 362px; top: 76px;
    width: 156px; height: 156px;
    border-radius: 50%;
    border: 4px solid var(--red);
    background: radial-gradient(circle at 50% 45%, #3a4a80, var(--navy));
    box-shadow: 0 0 0 3px var(--white);
  }
  .contact {
    position: absolute; left: 34px; top: 158px;
    font-size: 14px; color: var(--ink);
    line-height: 1.3;
  }
  .contact-address { margin-bottom: 8px; }
  .contact-line { display: flex; align-items: center; gap: 8px; }
  .contact-line svg { width: 13px; height: 13px; flex: none; }
  .slogan {
    position: absolute; right: 22px; bottom: 16px;
    color: var(--white);
    font-size: 14px;
    font-weight: 600;
  }
</style>
</head>
<body>

  <section class="card card--back" aria-label="Card back">
    <div class="brand-stack">Kelo<br>Wave<br>Mint</div>
  </section>

  <section class="card card--front" aria-label="Card front">
    <svg class="card-art" viewBox="0 0 540 315" preserveAspectRatio="none" aria-hidden="true">
      <path d="M0,315 L0,300 C140,305 250,275 320,205 C360,160 390,120 540,110 L540,315 Z" fill="var(--navy)"/>
      <path d="M56,282 C170,295 280,270 340,222" fill="none" stroke="var(--red)" stroke-width="6" stroke-linecap="round"/>
    </svg>

    <div class="corner-tab"></div>

    <div class="brand-stack">Kelo<br>Wave<br>Mint</div>

    <div class="person">
      <div class="person-name"><span class="first">Daren</span> <span class="last">Holloway</span></div>
      <div class="person-title">Co-Founder</div>
    </div>

    <div class="portrait" role="img" aria-label="Portrait photo of the co-founder"></div>

    <div class="contact">
      <div class="contact-address">418 Lindell Ave. Suite 310<br>Marlow Springs, TX 75990</div>
      <div class="contact-line">
        <svg viewBox="0 0 24 24"><path fill="#c1232a" d="M6.6 10.8a15 15 0 0 0 6.6 6.6l2.2-2.2a1 1 0 0 1 1-.25 11.4 11.4 0 0 0 3.6.57 1 1 0 0 1 1 1V20a1 1 0 0 1-1 1A17 17 0 0 1 3 4a1 1 0 0 1 1-1h3.5a1 1 0 0 1 1 1c0 1.25.2 2.45.57 3.57a1 1 0 0 1-.25 1z"/></svg>
        <span>(555) 214-0683</span>
      </div>
      <div class="contact-line">
        <svg viewBox="0 0 24 24"><rect x="2" y="5" width="20" height="14" rx="2" fill="#c1232a"/><path d="M3 6l9 7 9-7" fill="none" stroke="#fff" stroke-width="2"/></svg>
        <span>info@website.com</span>
      </div>
      <div class="contact-line">
        <svg viewBox="0 0 24 24"><circle cx="12" cy="12" r="10" fill="#c1232a"/><path d="M2 12h20M12 2c3 3 3 17 0 20M12 2c-3 3-3 17 0 20" fill="none" stroke="#fff" stroke-width="1.5"/></svg>
        <span>www.website.com</span>
      </div>
    </div>

    <div class="slogan">Making Every Wave Count</div>
  </section>

</body>
</html>
```